Vantiqo custom business card design

Need a authentic, innovative business card design for a new mobile app business. I am uploading a few screen images from our app for you to view. I would like app design theme to match business card design. I can also send logo images.

```html
<!DOCTYPE html>
<html lang="en">
<head>
<meta charset="utf-8">
<title>Vantiqo Business Card</title>
<link href="https://fonts.googleapis.com/css2?family=Open+Sans:wght@400;700&display=swap" rel="stylesheet">
<style>
  :root {
    --canvas: #e9e8ec;
    --purple: #5a0390;
    --purple-deep: #4a0078;
    --ink: #1b1b1b;
    --white: #ffffff;
    --paper: #f7f7f7;
    --grey-text: #5c5c5c;
    --pattern-purple: #e6dcf0;
    --pattern-grey: #e3e3e3;
  }
  * { box-sizing: border-box; margin: 0; padding: 0; }
  html, body { width: 1200px; height: 1000px; overflow: hidden; }
  body {
    background: var(--canvas);
    font-family: "Open Sans", Arial, sans-serif;
    position: relative;
  }
  .card {
    position: absolute;
    left: 250px;
    width: 700px;
    height: 400px;
    overflow: hidden;
    box-shadow: 0 6px 22px rgba(0,0,0,0.18);
  }
  .card-front { top: 70px; background: var(--purple); }
  .card-back { top: 530px; background: var(--white); }

  .front-shape { position: absolute; inset: 0; }

  .holder { position: absolute; left: 40px; top: 34px; color: var(--white); }
  .holder-name { font-weight: 700; font-size: 22px; letter-spacing: 0.3px; line-height: 1.1; }
  .holder-title { font-size: 15px; letter-spacing: 0.5px; line-height: 1.3; }

  .contact {
    position: absolute; left: 40px; top: 196px;
    color: var(--white); font-size: 17px; line-height: 24px;
    list-style: none;
  }
  .contact-address { margin-bottom: 2px; }
  .contact-line { display: flex; align-items: center; gap: 10px; }
  .contact-icon { width: 16px; height: 16px; flex: none; fill: var(--white); }

  .brand {
    position: absolute; left: 420px; top: 176px;
    display: flex; align-items: center; gap: 14px;
  }
  .brand-dot { width: 30px; height: 30px; border-radius: 50%; background: var(--purple); }
  .brand-name { font-weight: 700; font-size: 48px; color: var(--ink); letter-spacing: 0.5px; }

  .back-pattern {
    position: absolute; inset: 0;
    background: linear-gradient(135deg, var(--pattern-purple) 0%, var(--pattern-grey) 50%, var(--pattern-purple) 100%);
    opacity: 0.7;
  }
  .back-sign {
    position: absolute; right: 30px; bottom: 28px;
    display: flex; flex-direction: column; align-items: flex-end; gap: 6px;
  }
  .back-brand { display: flex; align-items: center; gap: 8px; }
  .back-brand-dot { width: 14px; height: 14px; border-radius: 50%; background: var(--purple); }
  .back-brand-name { font-weight: 700; font-size: 20px; color: var(--ink); }
  .back-url { font-size: 15px; color: var(--grey-text); letter-spacing: 0.3px; }
</style>
</head>
<body>

<section class="card card-front">
  <svg class="front-shape" width="700" height="400" viewBox="0 0 700 400" aria-hidden="true">
    <defs>
      <linearGradient id="panelWhite" x1="0" y1="0" x2="0" y2="1">
        <stop offset="0" stop-color="#ffffff"/>
        <stop offset="1" stop-color="#e8e8e8"/>
      </linearGradient>
      <linearGradient id="panelPurple" x1="0" y1="0" x2="0" y2="1">
        <stop offset="0" stop-color="#5c0494"/>
        <stop offset="1" stop-color="#4a0078"/>
      </linearGradient>
    </defs>
    <rect width="700" height="400" fill="url(#panelPurple)"/>
    <circle cx="620" cy="215" r="352" fill="var(--ink)"/>
    <circle cx="636" cy="215" r="344" fill="url(#panelWhite)"/>
  </svg>

  <header class="holder">
    <p class="holder-name">MARA LINDQVIST</p>
    <p class="holder-title">PRESIDENT</p>
  </header>

  <ul class="contact">
    <li class="contact-address">4127 Harborview Lane<br>Cedar Point, OR 97330</li>
    <li class="contact-line">
      <svg class="contact-icon" viewBox="0 0 16 16"><path d="M3 1h3l1 4-2 1c1 2 2 3 4 4l1-2 4 1v3c0 1-1 2-2 2C6 14 2 10 1 3c0-1 1-2 2-2z"/></svg>
      541 2098 7716
    </li>
    <li class="contact-line">
      <svg class="contact-icon" viewBox="0 0 16 16"><path d="M4 0h8v16H4zM5.5 2v10h5V2zM7 13.5h2v1H7z" fill-rule="evenodd"/></svg>
      541 6630 4182
    </li>
    <li class="contact-line">
      <svg class="contact-icon" viewBox="0 0 16 16"><path d="M4 1h7v4H4zM1 6h14v7h-3v2H4v-2H1zM5 10v4h6v-4z" fill-rule="evenodd"/></svg>
      541 7724 9051
    </li>
    <li class="contact-line">
      <svg class="contact-icon" viewBox="0 0 16 16"><path d="M1 3h14v10H1zM2 4.5v.5l6 4 6-4v-.5z" fill-rule="evenodd"/></svg>
      mara@vantiqo.com
    </li>
    <li class="contact-line">
      <svg class="contact-icon" viewBox="0 0 16 16"><circle cx="8" cy="8" r="7"/><path d="M1 8h14M8 1c3 3 3 11 0 14M8 1c-3 3-3 11 0 14" stroke="#5a0390" stroke-width="1.2" fill="none"/></svg>
      www.vantiqo.com
    </li>
  </ul>

  <div class="brand">
    <span class="brand-dot"></span>
    <span class="brand-name">Vantiqo</span>
  </div>
</section>

<section class="card card-back">
  <div class="back-pattern" role="img" aria-label="Faint repeating pattern of the brand symbol in light purple and grey"></div>
  <div class="back-sign">
    <div class="back-brand">
      <span class="back-brand-dot"></span>
      <span class="back-brand-name">Vantiqo</span>
    </div>
    <p class="back-url">www.vantiqo.com</p>
  </div>
</section>

</body>
</html>
```